Sci Fi/ Secret Agent Author needs website design!

My name is Lark Whitby and I am an author. I require a site that can provide information about myself and my books and other works.

I would like it to have a Home, blog function, (about the) books/series section so people can visit another section and read about each individual book that's going to be released. A resources page, a Store, social media links and ability to load/embed videos from clipvane and other.

I write mild scifi/thriller/conspiracy/secret government type novels. -At the moment-. The series follows a strong female lead that is an agent with a secret organisation in a classified military installation.

The theme would be professional yet possibly show this element.

/military fiction/thriller/fantasy/Sci fi/ femme-fatal, readers. Mostly females, age 18-60
Novel readers

5+ page

• Would like designers to follow brief. :)
• My budget includes all the pages I will need;
• eg home, blog, resources, store, ability to pay with coinpouch and Credit Cards
• , ability to have trailers from clipvane etc. Must have links to the social media mentioned in the brief.
• use of the colours I have suggested. electric/indigo purple, fuschia highlights , dark greys
• as I will possibly base branding for social media ETC on the look of your website design and colour scheme.
• Ability for trailer on front page??
• Should not be too cluttered. (But I am open to all ideas)

```html
<!DOCTYPE html>
<html lang="en">
<head>
<meta charset="utf-8">
<title>Lark Whitby — Conspiracy Novels</title>
<link rel="stylesheet" href="https://fonts.googleapis.com/css2?family=Open+Sans:wght@400;600&family=Oswald:wght@400;500&family=Zilla+Slab:wght@600;700&display=swap">
<style>
:root{
  --indigo:#4b1a9c;
  --indigo-soft:#7b46c9;
  --lilac:#c9a8f0;
  --plum:#3d2a52;
  --ink:#1e1e1e;
  --text:#333;
  --muted:#8a8a8a;
  --light:#ececee;
  --footer:#2b2b2b;
  --white:#fff;
}
*{box-sizing:border-box;margin:0;padding:0}
html,body{width:1200px;height:2691px;overflow:hidden}
body{font-family:"Open Sans",Arial,sans-serif;color:var(--text);background:var(--white)}
.wrap{width:1020px;margin:0 auto;position:relative;height:100%}

/* header */
.site-header{height:106px}
.brand{position:absolute;left:0;top:31px;font-family:"Zilla Slab",Georgia,serif;font-weight:700;font-size:36px;color:var(--indigo);letter-spacing:.5px}
.main-nav{position:absolute;right:0;top:38px;display:flex;align-items:center;gap:30px;font-size:15px;color:var(--ink)}
.main-nav .active{border:1px solid var(--indigo-soft);border-radius:18px;padding:5px 14px;color:var(--indigo)}
.cart{display:flex;align-items:center;gap:4px;color:var(--indigo);font-size:13px}

/* hero */
.hero{height:581px;position:relative;background:linear-gradient(100deg,#15121c 0%,#2a1d2a 35%,#1a1720 60%,#0e0d12 100%);overflow:hidden}
.hero-photo{position:absolute;inset:0;background:radial-gradient(circle at 42% 35%,rgba(120,40,50,.35),transparent 40%)}
.hero-copy{position:absolute;left:90px;top:260px;color:var(--white)}
.hero-copy .name{font-size:56px;color:var(--lilac);line-height:1.1;letter-spacing:1px}
.hero-copy .tag{font-size:40px;line-height:1.2;letter-spacing:1px}
.hero-copy .sub{font-size:26px;margin-top:4px}
.book{position:absolute;left:753px;top:55px;width:314px;height:481px;background:linear-gradient(160deg,#6c7078,#2e3036 55%,#1b1c20);box-shadow:12px 10px 24px rgba(0,0,0,.6);border-right:12px solid #d8d8d8}
.dots{position:absolute;left:92px;top:542px;display:flex;gap:4px}
.dots span{width:14px;height:14px;border-radius:50%;background:var(--white)}
.dots span:first-child{background:var(--indigo-soft)}

/* author */
.author{height:336px;background:linear-gradient(120deg,#43305a,#382850 50%,#42305a);color:var(--white)}
.author-photo{position:absolute;left:34px;top:52px;width:230px;height:230px;border-radius:50%;background:radial-gradient(circle at 50% 40%,#e8d2b8,#b9a58f 70%);border:3px solid rgba(255,255,255,.5)}
.author-body{position:absolute;left:283px;top:70px;width:700px}
.author-body h2{font-weight:400;font-size:27px;margin-bottom:10px}
.author-body p{font-size:13.5px;line-height:1.62}
.btn{display:inline-block;border:1px solid currentColor;border-radius:18px;padding:7px 18px;font-size:13px;margin-top:16px}
.author .btn{border-color:rgba(255,255,255,.8)}

/* resources */
.resources{height:439px}
.resources-copy{position:absolute;left:0;top:102px;width:477px}
.resources-copy h2{font-weight:400;font-size:27px;color:var(--ink);margin-bottom:14px}
.resources-copy p{font-size:13.5px;line-height:1.7;color:var(--muted);text-align:justify}
.resources .btn{color:var(--indigo);border-color:var(--indigo-soft);margin-top:20px}
.video{position:absolute;left:504px;top:78px;width:514px;height:295px;border:5px solid #e6e6e6;background:#fff}
.video-frame{width:100%;height:100%;background:linear-gradient(180deg,#3d3f52,#2a2436 55%,#4a2f45);position:relative}
.play{position:absolute;left:50%;top:50%;transform:translate(-50%,-50%)}

/* store */
.store{height:542px;background:var(--light)}
.section-title{text-align:center;font-weight:400;font-size:27px;color:var(--ink)}
.store .section-title{padding-top:68px}
.store-grid{position:absolute;top:140px;left:-1px;display:flex;gap:18px}
.store-tile{width:242px;height:294px;position:relative;display:flex;align-items:flex-end;justify-content:center;padding-bottom:22px;border:3px solid #fff;box-shadow:0 1px 4px rgba(0,0,0,.2)}
.store-tile span{font-family:"Oswald",Arial,sans-serif;font-size:29px;color:var(--white);text-transform:uppercase}
.t1{background:linear-gradient(160deg,#6b4a4a,#3f2a2e)}
.t2{background:linear-gradient(160deg,#4a3236,#1e1618)}
.t3{background:radial-gradient(circle at 50% 35%,#8a6a3a,#1a120c 60%)}
.t4{background:linear-gradient(180deg,#2f4fa8,#1a2452)}

/* blog */
.blog{height:384px}
.blog .section-title{padding-top:78px}
.posts{position:absolute;top:156px;left:2px;display:flex;gap:95px}
.post{display:flex;gap:16px;width:462px}
.post-thumb{width:162px;height:142px;flex:none}
.p1{background:linear-gradient(160deg,#5a6a78,#2a323a)}
.p2{background:linear-gradient(160deg,#8a8e94,#44474c)}
.post h3{font-weight:400;font-size:15px;color:var(--ink);margin-top:6px}
.post time{display:block;font-size:13px;color:var(--ink);margin:8px 0 6px}
.post p{font-size:11.5px;line-height:1.65;color:#444}
.post a{display:block;font-size:12.5px;color:var(--indigo);margin-top:4px;text-decoration:none}

/* footer */
.site-footer{height:303px;background:var(--footer);color:var(--white)}
.footer-brand{position:absolute;left:0;top:107px;font-family:"Zilla Slab",Georgia,serif;font-weight:600;font-size:32px;color:#cfcfcf}
.col{position:absolute;top:52px}
.col h4{font-weight:400;font-size:15px;margin-bottom:20px}
.contact{left:292px;font-size:11.5px;line-height:2}
.mailing{left:558px;width:240px}
.mailing p{font-size:11px;line-height:1.6;margin-top:-6px}
.signup{display:flex;margin-top:12px}
.signup .field{width:148px;height:30px;background:#fff;color:#999;font-size:10.5px;padding:8px 8px}
.signup .go{width:55px;height:30px;background:var(--indigo);font-size:11px;padding:8px 0;text-align:center}
.social{left:845px}
.social ul{list-style:none;display:grid;grid-template-columns:auto auto;gap:8px 14px;font-size:12px}
.social li{display:flex;align-items:center;gap:6px}
.social li::before{content:"";width:10px;height:10px;background:#e6e6e6;border-radius:2px}
.rule{position:absolute;left:0;right:0;top:220px;border-top:1px solid #777}
.copyright{position:absolute;left:0;right:0;top:254px;text-align:center;font-size:12px}
</style>
</head>
<body>

<header class="site-header">
  <div class="wrap">
    <div class="brand">LARK WHITBY</div>
    <nav class="main-nav">
      <span class="active">HOME</span>
      <span>ABOUT THE BOOK</span>
      <span>RESOURCES</span>
      <span>STORE</span>
      <span>BLOG</span>
      <span>CONTACT US</span>
      <span class="cart">
        <svg width="16" height="14" viewBox="0 0 16 14"><path d="M0 1h3l2 8h8l2-6H4" fill="none" stroke="currentColor" stroke-width="2"/><circle cx="6" cy="12" r="1.5" fill="currentColor"/><circle cx="12" cy="12" r="1.5" fill="currentColor"/></svg>: 0
      </span>
    </nav>
  </div>
</header>

<section class="hero">
  <div class="hero-photo" role="img" aria-label="Dark atmospheric photo of a woman in costume makeup in a shadowy forest"></div>
  <div class="hero-copy">
    <div class="name">LARK WHITBY</div>
    <div class="tag">CONSPIRACY NOVELS</div>
    <div class="sub">Neque porro quisquam est qui ipsum</div>
  </div>
  <div class="book" role="img" aria-label="Hardcover book with a cover photo of a cloaked woman on a stormy hillside"></div>
  <div class="dots"><span></span><span></span><span></span></div>
</section>

<section class="author">
  <div class="wrap">
    <div class="author-photo" role="img" aria-label="Portrait photo of the author"></div>
    <div class="author-body">
      <h2>AUTHOR</h2>
      <p>It is a long established fact that a reader will be distracted by the readable content of a page when looking at its layout. The point of using Lorem Ipsum is that it has a more-or-less normal distribution of letters, as opposed to using 'Content here, content here', making it look like readable English. Many desktop publishing packages and web page editors now use Lorem Ipsum as their default model text, and a search for 'lorem ipsum' will uncover many web sites still in their infancy.</p>
      <span class="btn">READ MORE »</span>
    </div>
  </div>
</section>

<section class="resources">
  <div class="wrap">
    <div class="resources-copy">
      <h2>RESOURCES</h2>
      <p>It is a long established fact that a reader will be distracted by the readable content of a page when looking at its layout. The point of using Lorem Ipsum is that it has a more-or-less normal distribution of letters, as opposed to using 'Content here, content here', making it look like readable English. Many desktop publishing packages and web page editors now use Lorem Ipsum as their default model text, and a search for 'lorem ipsum' will uncover many web sites still in their infancy.</p>
      <span class="btn">Read More »</span>
    </div>
    <div class="video">
      <div class="video-frame" role="img" aria-label="Trailer still of a hooded figure sitting between library shelves">
        <svg class="play" width="64" height="64" viewBox="0 0 64 64"><circle cx="32" cy="32" r="31" fill="rgba(20,20,20,.75)"/><path d="M25 19l21 13-21 13z" fill="#fff"/></svg>
      </div>
    </div>
  </div>
</section>

<section class="store">
  <div class="wrap">
    <h2 class="section-title">STORE</h2>
    <div class="store-grid">
      <div class="store-tile t1" role="img" aria-label="Book cover photo of a doll lying in autumn leaves"><span>Thriller</span></div>
      <div class="store-tile t2" role="img" aria-label="Book cover photo of a woman holding a rose"><span>Conspiracy</span></div>
      <div class="store-tile t3" role="img" aria-label="Book cover photo of a candle on a skull and old books"><span>Thriller</span></div>
      <div class="store-tile t4" role="img" aria-label="Book cover photo of an owl in a blue stone archway"><span>Secret Agent</span></div>
    </div>
  </div>
</section>

<section class="blog">
  <div class="wrap">
    <h2 class="section-title">LATEST BLOG</h2>
    <div class="posts">
      <article class="post">
        <div class="post-thumb p1" role="img" aria-label="Photo of a woman in a dark gown by a river"></div>
        <div>
          <h3>Nemo Enim Ipsam Volup</h3>
          <time>09-07-2017</time>
          <p>Lorem Ipsum has been the industry's standard dummy text ever since the 1500s, when an unknown printer took a galley of type and scrambled it to make a type specimen</p>
          <a>Read More &gt;&gt;</a>
        </div>
      </article>
      <article class="post">
        <div class="post-thumb p2" role="img" aria-label="Photo of a woman standing by a stone wall"></div>
        <div>
          <h3>Nemo Enim Ipsam Volup</h3>
          <time>09-07-2017</time>
          <p>Lorem Ipsum has been the industry's standard dummy text ever since the 1500s, when an unknown printer took a galley of type and scrambled it to make a type specimen</p>
          <a>Read More &gt;&gt;</a>
        </div>
      </article>
    </div>
  </div>
</section>

<footer class="site-footer">
  <div class="wrap">
    <div class="footer-brand">LARK WHITBY</div>
    <div class="col contact">
      <h4>CONTACT US</h4>
      <div>Address : 12 Fenwick Lane, Harrow Quay<br>Bristol, QX4 7LM<br>Phone : 555-018-4420.<br>Email : hello@larkwhitby.test</div>
    </div>
    <div class="col mailing">
      <h4>JOIN OUR MAILING LIST</h4>
      <p>Your about us information would fit here nicely.</p>
      <div class="signup"><span class="field">Email address</span><span class="go">Submit</span></div>
    </div>
    <div class="col social">
      <h4>FOLLOW US OUT THERE</h4>
      <ul>
        <li>Friendwall</li>
        <li>Chirpline</li>
        <li>Linkpro</li>
        <li>Circleplus</li>
      </ul>
    </div>
    <div class="rule"></div>
    <div class="copyright">Copyright © 2017. All Rights Reserved</div>
  </div>
</footer>

</body>
</html>
```